holloway paving service

Needs to have phone number 0418259730 and email markholloway@brightmail.com.au.
ABN 62318470915
name mark holloway

For all your concreting solutions
Excavation
Exposed & colour concrete
House & shed slabs
Driveways
Landing & steps

Contact Information for Business Card

ph 0418259730
email markholloway@brightmail.com.au.
ABN 62318470915
name mark holloway

```html
<!DOCTYPE html>
<html lang="en">
<head>
<meta charset="utf-8">
<title>Holloway Paving Service – Business Card</title>
<link href="https://fonts.googleapis.com/css2?family=Montserrat:wght@500;600;700&family=Quicksand:wght@500;600&display=swap" rel="stylesheet">
<style>
  :root {
    --backdrop: #4a3b31;
    --card-white: #f1f1f1;
    --card-white-edge: #dcdcdc;
    --brand-orange: #f06a24;
    --brand-orange-deep: #d9571a;
    --brand-orange-soft: #f58a4e;
    --charcoal: #5e5e5e;
    --ink-white: #ffffff;
  }
  * { box-sizing: border-box; margin: 0; padding: 0; }
  html, body {
    width: 1200px; height: 960px; overflow: hidden;
    background: var(--backdrop);
  }
  .canvas { position: relative; width: 1200px; height: 960px; }

  /* Front of card */
  .card-front {
    position: absolute; left: 302px; top: 127px;
    width: 600px; height: 341px;
    background: linear-gradient(135deg, #f7f7f7 0%, var(--card-white) 60%, var(--card-white-edge) 100%);
    box-shadow: 0 6px 14px rgba(0,0,0,0.45);
    overflow: hidden;
  }
  .brand-lockup {
    position: absolute; left: 92px; top: 66px;
    display: flex; align-items: center;
  }
  .brand-square {
    width: 74px; height: 74px; background: var(--brand-orange);
  }
  .brand-divider {
    width: 2px; height: 108px; background: var(--brand-orange);
    margin: 0 14px 0 28px;
  }
  .brand-name {
    font-family: 'Montserrat', sans-serif; font-weight: 700;
    font-size: 22px; line-height: 26px; letter-spacing: 0.2px;
    color: var(--brand-orange); text-transform: uppercase;
  }
  .brand-phone {
    font-family: 'Montserrat', sans-serif; font-weight: 500;
    font-size: 17px; letter-spacing: 1.5px;
    color: var(--brand-orange); margin-top: 6px;
  }
  .contact-band {
    position: absolute; left: 0; top: 221px;
    width: 100%; height: 98px;
    background: linear-gradient(90deg, var(--brand-orange) 0%, var(--brand-orange) 60%, var(--brand-orange-deep) 100%);
    border-top: 3px solid var(--charcoal);
    border-bottom: 2px solid #f3f3f3;
    box-shadow: 0 2px 0 #bdbdbd;
    text-align: center; color: var(--ink-white);
    padding-top: 17px;
  }
  .contact-name {
    font-family: 'Montserrat', sans-serif; font-weight: 700;
    font-size: 22px; letter-spacing: 0.3px; text-transform: uppercase;
    line-height: 26px;
  }
  .contact-line {
    font-family: 'Quicksand', sans-serif; font-weight: 500;
    font-size: 14px; line-height: 20px;
  }

  /* Back of card */
  .card-back {
    position: absolute; left: 300px; top: 500px;
    width: 598px; height: 342px;
    background: linear-gradient(90deg, var(--brand-orange-soft) 0%, var(--brand-orange) 55%, var(--brand-orange-deep) 100%);
    box-shadow: 0 6px 14px rgba(0,0,0,0.45);
    overflow: hidden;
  }
  .back-pattern-area {
    position: absolute; inset: 0;
    background: linear-gradient(180deg, rgba(255,255,255,0.04), rgba(0,0,0,0.04));
  }
  .back-brand {
    position: absolute; left: 112px; top: 140px;
    display: flex; align-items: center; gap: 10px;
  }
  .back-brand-square { width: 22px; height: 22px; background: var(--ink-white); }
  .back-brand-name {
    font-family: 'Montserrat', sans-serif; font-weight: 700;
    font-size: 13px; line-height: 17px; color: var(--ink-white);
    text-transform: uppercase;
  }
  .service-list {
    position: absolute; left: 252px; top: 124px;
    list-style: none;
    font-family: 'Quicksand', sans-serif; font-weight: 500;
    font-size: 14px; line-height: 18px; color: var(--ink-white);
    letter-spacing: 0.3px;
  }
  .service-list li { display: flex; align-items: center; }
  .service-list li::before {
    content: ""; width: 5px; height: 5px; background: var(--ink-white);
    transform: rotate(45deg); margin-right: 9px;
  }
</style>
</head>
<body>
<main class="canvas">
  <section class="card-front" aria-label="Business card front">
    <div class="brand-lockup">
      <div class="brand-square"></div>
      <div class="brand-divider"></div>
      <div class="brand-text">
        <div class="brand-name">Holloway Paving<br>Service</div>
        <div class="brand-phone">0418259730</div>
      </div>
    </div>
    <div class="contact-band">
      <div class="contact-name">Mark Holloway</div>
      <div class="contact-line">markholloway@brightmail.com.au</div>
      <div class="contact-line">ABN 62318470915</div>
    </div>
  </section>

  <section class="card-back" aria-label="Business card back">
    <div class="back-pattern-area" role="img" aria-label="Subtle repeating brand pattern on orange"></div>
    <div class="back-brand">
      <div class="back-brand-square"></div>
      <div class="back-brand-name">Holloway<br>Paving<br>Service</div>
    </div>
    <ul class="service-list">
      <li>Excavation</li>
      <li>Exposed &amp; colour concrete</li>
      <li>House &amp; shed slabs</li>
      <li>Driveways</li>
      <li>Landing &amp; steps</li>
    </ul>
  </section>
</main>
</body>
</html>
```